Classy, Elegant, Simple Business Card Design

Looking to have a classy, simple, and elegant design. Want a top notch designed business card. I really like the look of the new torvane credit card. I also like the design I attached. I am trying to reach 21-29 year old females for booking us for there wedding or event. We offer Disc Jockey Service, Photo Booth Rentals, and Uplighting .

Target Market(s)

21-28 year old females

Contact Information for Business Card

Has to have logo, website, email, and phone number

Font styles to use
Other font styles liked:
• open to font choice, modern, clean
Designer to choose
33a6d7
0791cd
0555a3
ffffff

Requirements
Must have
• Has to have logo, website, email, and phone number
Nice to have
• I really like the design of the new torvane credit card. I also included my logo and some designs I like
Should not have
• clutter or too much info

```html
<!DOCTYPE html>
<html lang="en">
<head>
<meta charset="utf-8">
<title>Tideline Event Group – Business Card</title>
<link rel="stylesheet" href="https://fonts.googleapis.com/css2?family=Poppins:wght@400;500&display=swap">
<style>
  :root {
    --bg: #1c1c1c;
    --card: #ffffff;
    --blue: #0791cd;
    --blue-deep: #0555a3;
    --text: #444444;
    --muted: #9a9a9a;
    --rule: #cfcfcf;
  }
  * { margin: 0; padding: 0; box-sizing: border-box; }
  html, body {
    width: 1200px; height: 1200px; overflow: hidden;
    background: var(--bg);
    font-family: "Poppins", sans-serif;
  }
  .card {
    position: absolute;
    left: 257px;
    width: 686px; height: 392px;
    background: var(--card);
  }
  .card--front { top: 165px; }
  .card--back { top: 653px; }

  .identity {
    position: absolute;
    right: 390px; top: 168px;
    text-align: right;
  }
  .identity__name {
    font-size: 24px; font-weight: 500; line-height: 1.1;
    color: var(--blue); letter-spacing: 0.3px;
  }
  .identity__title {
    font-size: 15px; color: var(--muted); margin-top: 3px;
  }
  .divider {
    position: absolute; left: 315px; top: 165px;
    width: 1px; height: 61px; background: var(--rule);
  }
  .contact {
    position: absolute; left: 334px; top: 162px;
    list-style: none;
  }
  .contact li {
    display: flex; align-items: center;
    font-size: 16px; line-height: 19.5px; color: var(--text);
  }
  .contact svg { width: 12px; height: 12px; margin-right: 9px; flex: none; }
  .services {
    position: absolute; left: 0; right: 0; top: 333px;
    text-align: center; font-size: 16px; color: var(--text);
  }
  .services .dot { color: var(--blue); margin: 0 3px; }

  .brand {
    position: absolute; inset: 0;
    display: flex; align-items: center; justify-content: center; gap: 14px;
  }
  .brand__mark {
    width: 22px; height: 22px; border-radius: 50%; background: var(--blue-deep);
  }
  .brand__name {
    font-size: 34px; font-weight: 500; color: var(--blue-deep); letter-spacing: 0.5px;
  }
</style>
</head>
<body>
  <section class="card card--front">
    <div class="identity">
      <div class="identity__name">Daniel Harlow</div>
      <div class="identity__title">President</div>
    </div>
    <div class="divider"></div>
    <ul class="contact">
      <li>
        <svg viewBox="0 0 12 12" aria-hidden="true"><path fill="#0791cd" d="M2.6 0.5l2 2.2-1 1.4c0.7 1.6 1.8 2.7 3.3 3.4l1.4-1 2.2 2-1 2C5.2 10.8 1.2 6.8 0.5 1.5z"/></svg>
        555-201-4870
      </li>
      <li>
        <svg viewBox="0 0 12 12" aria-hidden="true"><rect x="0.5" y="2.5" width="11" height="7.5" fill="#0791cd"/><path d="M0.8 2.8L6 7l5.2-4.2" stroke="#fff" stroke-width="1" fill="none"/></svg>
        info@tidelineevents.com
      </li>
      <li>
        <svg viewBox="0 0 12 12" aria-hidden="true"><circle cx="6" cy="6" r="5.5" fill="#0791cd"/><path d="M3 4c1 0 2 1 1.5 2S3 7.5 3.5 9M7 2c0 1.2 1.5 1.5 2.5 1.2M6.5 6.5c1 0 2 .8 2 2" stroke="#fff" stroke-width="1" fill="none"/></svg>
        www.tidelineevents.com
      </li>
    </ul>
    <p class="services">Disc Jockey Service<span class="dot">•</span>Photo Booth Rentals<span class="dot">•</span>Uplighting .</p>
  </section>

  <section class="card card--back">
    <div class="brand">
      <span class="brand__mark"></span>
      <span class="brand__name">Tideline Event Group</span>
    </div>
  </section>
</body>
</html>
```